International Petrochemical business needs a web design for Clearway Desk system

We need a web design for a "Clearway Desk" system for an international petrochemical company. The web site is used internally within the company. It is hosted by an internal department which provides government permit request service for other departments.

We would like to see designs of two pages using color light blue. (home page, internal page as attached).
Home Page:
1. Header has a background image and small animation. Header on home page can be taller than the header of the internal page.
2. Layout as attached.

Internal Page:
1. Header can use the same background image as the home page and can be shorter to utilize the page for content.
2. The blue icon behind every captions represent an icon. When user move mouse over this icon, it displays the caption in Thai language as a tooltip. This icon needs to be redesign.

The final design should communicate the followings:
- Excellent service provided system in terms of time and accurary
- Rapid growth of business via building petrochemical refinery plant
Updates

For Internal Page, the blue circle behind every captions represent an icon. When mouse over this icon, a tool tip showing the caption in Thai language is shown. Please also design this icon..

There are more feedbacks from customer as followed:

1. Banner should consists of 
    1.1 "Approved" stamp on paper
    1.2 An image of Garuda. It is used on every government documents in Thailand
    1.3 Image of petrochemical plant
2. Each menu item (Home, Permit, Search, etc) should have different colors. Drop down menu will use the same color as its parent menu item.
3. Overall tone of the web page should be light blue with background of the body the web page in white
4. "New Request" button should use green color with icon on it
5. Table header of each box in the body of the page should use dark blue background with text in white

Please kindly submit your revisions.
Thank you.

Industry/Entity Type

Business

Requirements
Must have
• 1. Design for 1024x768 screen resolution
2. Use light blue theme
3. Background of header where the company logo is must have white background

```html
<!DOCTYPE html>
<html lang="en">
<head>
<meta charset="utf-8">
<title>Clearway Desk – Home</title>
<link href="https://fonts.googleapis.com/css2?family=Open+Sans:wght@400;600;700&display=swap" rel="stylesheet">
<style>
:root{
  --page-bg:#ffffff;
  --nav-top:#8fdcf8;
  --nav-bottom:#4cc0ee;
  --nav-divider:#3aa9d8;
  --nav-divider-light:#a6e4fa;
  --brand-blue:#1b9ad6;
  --brand-ink:#1e3f8f;
  --link:#3aa8df;
  --text:#555555;
  --text-soft:#6b6b6b;
  --panel-bg:#f4f4f4;
  --panel-head-top:#fbfbfb;
  --panel-head-bottom:#e4e4e4;
  --rule:#e2e2e2;
  --button-top:#86d6f7;
  --button-bottom:#3bb6ea;
  --sun-core:#f6b40e;
  --sun-edge:#e07b06;
  --footer-bg:#e6e6e6;
  --hero-sky:#d58a6a;
  --hero-dusk:#7a5a86;
  --hero-ground:#1c1d28;
}
*{box-sizing:border-box;margin:0;padding:0}
html,body{width:1193px;height:1200px;overflow:hidden;background:var(--page-bg)}
body{font-family:"Open Sans",Arial,sans-serif;color:var(--text)}
.stage{position:relative;width:1024px;height:1030px;transform:scale(1.16504);transform-origin:0 0}
.abs{position:absolute}

/* brand */
.brand{left:40px;top:14px;display:flex;align-items:center;gap:6px}
.brand-dot{width:24px;height:24px;border-radius:50%;background:var(--brand-blue)}
.brand-name{font-size:14px;font-weight:700;color:var(--brand-ink);line-height:1;letter-spacing:.2px}

/* navigation */
.main-nav{left:32px;top:64px;width:961px;height:55px;background:linear-gradient(var(--nav-top),var(--nav-bottom))}
.nav-item{position:absolute;top:0;height:55px;display:flex;align-items:center;justify-content:center;color:#fff;font-size:14px;border-right:1px solid var(--nav-divider);box-shadow:1px 0 0 var(--nav-divider-light)}
.nav-search{position:absolute;left:661px;top:12px;width:286px;height:29px;border-radius:15px;background:#fff;border:1px solid #cfe6f2;display:flex;align-items:center;padding:0 12px 0 16px;font-size:10px;color:#777;justify-content:space-between}

/* hero */
.hero{left:32px;top:119px;width:960px;height:254px;background:linear-gradient(180deg,var(--hero-dusk) 0%,var(--hero-sky) 28%,#6b5566 45%,var(--hero-ground) 70%,#2c2a33 100%)}
.hero-arrow{position:absolute;top:112px;width:34px;height:34px}

/* panels */
.panel{position:absolute;background:var(--panel-bg);border:1px solid #ececec}
.panel-title{height:36px;padding-left:19px;display:flex;align-items:center;font-size:14px;color:#333;background:linear-gradient(var(--panel-head-top),var(--panel-head-bottom))}
.grid{width:100%;border-collapse:collapse;table-layout:fixed;font-size:12.5px}
.grid th{font-weight:400;color:#444;border-bottom:1px solid var(--rule);border-right:1px solid var(--rule)}
.grid td{text-align:center;border-right:1px solid var(--rule);padding:0}
.grid th:last-child,.grid td:last-child{border-right:none}
.grid .filler td{border-bottom:1px solid var(--rule)}
.grid a{color:var(--link);text-decoration:none}
.grid .branch{font-weight:700;color:#555}
.grid .status{text-align:left;padding-left:11px;font-size:10.5px;color:var(--text-soft)}
.sun{display:inline-block;vertical-align:middle;margin-left:28px}
.pager{display:flex;align-items:center;gap:14px;padding-left:13px;font-size:12.5px;color:#444}
.pager svg{display:block}

/* call to action */
.new-request{left:522px;top:752px;width:381px;height:37px;background:linear-gradient(var(--button-top),var(--button-bottom));border:1px solid #3aa6d6;display:flex;align-items:center;justify-content:center;color:#fff;font-size:21px;font-weight:600;letter-spacing:.5px}

/* footer */
.site-footer{left:0;top:975px;width:1024px;height:55px;background:var(--footer-bg);font-size:11px;color:#333}
.footer-links{position:absolute;left:42px;top:16px;display:flex;gap:26px}
.copyright{position:absolute;left:728px;top:15px}
</style>
</head>
<body>
<div class="stage">

  <div class="abs brand"><span class="brand-dot"></span><span class="brand-name">NORTHGATE CHEMICAL</span></div>

  <nav class="abs main-nav">
    <span class="nav-item" style="left:0;width:96px">Home</span>
    <span class="nav-item" style="left:96px;width:113px">Permits</span>
    <span class="nav-item" style="left:209px;width:106px">Search</span>
    <span class="nav-item" style="left:315px;width:106px">Report</span>
    <span class="nav-item" style="left:421px;width:94px">Admin</span>
    <span class="nav-item" style="left:515px;width:73px">Help</span>
    <div class="nav-search">Search
      <svg width="16" height="16" viewBox="0 0 16 16"><circle cx="6" cy="6" r="4.3" fill="none" stroke="#888" stroke-width="1.8"/><line x1="9.2" y1="9.2" x2="14" y2="14" stroke="#888" stroke-width="2.4" stroke-linecap="round"/></svg>
    </div>
  </nav>

  <div class="abs hero" role="img" aria-label="Petrochemical refinery plant lit at dusk beside a river">
    <svg class="hero-arrow" style="left:24px" viewBox="0 0 34 34"><circle cx="17" cy="17" r="16" fill="#fff"/><path d="M26 17H10M16 10l-7 7 7 7" fill="none" stroke="#111" stroke-width="3.4"/></svg>
    <svg class="hero-arrow" style="left:902px" viewBox="0 0 34 34"><circle cx="17" cy="17" r="16" fill="#fff"/><path d="M8 17h16M18 10l7 7-7 7" fill="none" stroke="#111" stroke-width="3.4"/></svg>
  </div>

  <!-- New Requests -->
  <section class="panel" style="left:122px;top:382px;width:380px;height:197px">
    <div class="panel-title">New Requests</div>
    <table class="grid">
      <colgroup><col style="width:111px"><col style="width:163px"><col></colgroup>
      <thead><tr style="height:28px"><th>Request No.</th><th>Request Date</th><th>Branch</th></tr></thead>
      <tbody>
        <tr style="height:56px"><td><a href="#">56-0003</a></td><td>20/4/2013</td><td class="branch">GC1</td></tr>
        <tr class="filler" style="height:38px;vertical-align:top"><td style="padding-top:7px"><a href="#">56-0004</a></td><td style="padding-top:7px">21/4/2013</td><td class="branch" style="padding-top:4px">GC2</td></tr>
      </tbody>
    </table>
    <div class="pager" style="height:38px">
      <svg width="8" height="12" viewBox="0 0 8 12"><path d="M6 1L1.5 6 6 11" fill="none" stroke="#3aa8df" stroke-width="2"/></svg><span>1</span><span>2</span><span>3</span><span>4</span><svg width="8" height="12" viewBox="0 0 8 12"><path d="M2 1l4.5 5L2 11" fill="none" stroke="#3aa8df" stroke-width="2"/></svg>
    </div>
  </section>

  <!-- New Working Requests -->
  <section class="panel" style="left:522px;top:382px;width:380px;height:197px">
    <div class="panel-title">New Working Requests</div>
    <table class="grid">
      <colgroup><col style="width:111px"><col style="width:132px"><col></colgroup>
      <thead><tr style="height:28px"><th>Request No.</th><th>Request Date</th><th>Status</th></tr></thead>
      <tbody>
        <tr style="height:24px;vertical-align:bottom"><td><a href="#">56-0003</a></td><td>20/4/2013</td><td class="status">Waiting for proces</td></tr>
        <tr style="height:22px"><td><a href="#">56-0004</a></td><td>21/4/2013</td><td class="status">In Progress</td></tr>
        <tr style="height:22px"><td><a href="#">56-0003</a></td><td>20/4/2013</td><td class="status">Incomplete Document</td></tr>
        <tr class="filler" style="height:26px;vertical-align:top"><td style="padding-top:2px"><a href="#">56-0004</a></td><td style="padding-top:2px">21/4/2013</td><td class="status" style="padding-top:2px">Cancel Requested</td></tr>
      </tbody>
    </table>
    <div class="pager" style="height:38px">
      <svg width="8" height="12" viewBox="0 0 8 12"><path d="M6 1L1.5 6 6 11" fill="none" stroke="#3aa8df" stroke-width="2"/></svg><span>1</span><span>2</span><span>3</span><span>4</span><svg width="8" height="12" viewBox="0 0 8 12"><path d="M2 1l4.5 5L2 11" fill="none" stroke="#3aa8df" stroke-width="2"/></svg>
    </div>
  </section>

  <!-- Expiring Permits -->
  <section class="panel" style="left:122px;top:587px;width:780px;height:157px">
    <div class="panel-title">Expiring Permits</div>
    <table class="grid">
      <colgroup><col style="width:111px"><col style="width:163px"><col style="width:168px"><col style="width:80px"><col style="width:148px"><col></colgroup>
      <thead><tr style="height:30px"><th>Permit No.</th><th>Expire Date</th><th>Permit Name</th><th>Branch</th><th>Required Time (Day)</th><th>Due Date</th></tr></thead>
      <tbody>
        <tr style="height:26px"><td><a href="#">AB56001</a></td><td>20/4/2013</td><td>Permit Name ### 10</td><td>GC1</td><td style="padding-left:30px">30<svg class="sun" width="16" height="16" viewBox="0 0 16 16"><circle cx="8" cy="8" r="7" fill="#ffd66a"/><circle cx="8" cy="8" r="5.5" fill="var(--sun-core)" stroke="var(--sun-edge)"/></svg></td><td>-40</td></tr>
        <tr class="filler" style="height:35px;vertical-align:top"><td style="padding-top:6px"><a href="#">BI05502</a></td><td style="padding-top:6px">21/4/2013</td><td style="padding-top:6px">Permit Name ### 20</td><td style="padding-top:6px">GC2</td><td style="padding-top:5px;padding-left:30px">60<svg class="sun" width="16" height="16" viewBox="0 0 16 16"><circle cx="8" cy="8" r="7" fill="#ffd66a"/><circle cx="8" cy="8" r="5.5" fill="var(--sun-core)" stroke="var(--sun-edge)"/></svg></td><td style="padding-top:6px">15</td></tr>
      </tbody>
    </table>
    <div class="pager" style="height:30px">
      <svg width="8" height="12" viewBox="0 0 8 12"><path d="M6 1L1.5 6 6 11" fill="none" stroke="#3aa8df" stroke-width="2"/></svg><span>1</span><span>2</span><span>3</span><span>4</span><svg width="8" height="12" viewBox="0 0 8 12"><path d="M2 1l4.5 5L2 11" fill="none" stroke="#3aa8df" stroke-width="2"/></svg>
    </div>
  </section>

  <!-- My Requests -->
  <section class="panel" style="left:122px;top:752px;width:380px;height:214px">
    <div class="panel-title">New Requests</div>
    <table class="grid">
      <colgroup><col style="width:112px"><col style="width:133px"><col></colgroup>
      <thead><tr style="height:48px"><th>Request No.</th><th>Request Date</th><th>Status</th></tr></thead>
      <tbody>
        <tr style="height:42px"><td><a href="#">56-00001</a></td><td>20/4/2013</td><td class="status">Waiting for proces</td></tr>
        <tr class="filler" style="height:56px;vertical-align:top"><td style="padding-top:4px"><a href="#">56-00002</a></td><td style="padding-top:4px">21/4/2013</td><td class="status" style="padding-top:5px">In Progress</td></tr>
      </tbody>
    </table>
    <div class="pager" style="height:30px">
      <svg width="8" height="12" viewBox="0 0 8 12"><path d="M6 1L1.5 6 6 11" fill="none" stroke="#3aa8df" stroke-width="2"/></svg><span>1</span><span>2</span><span>3</span><span>4</span><svg width="8" height="12" viewBox="0 0 8 12"><path d="M2 1l4.5 5L2 11" fill="none" stroke="#3aa8df" stroke-width="2"/></svg>
    </div>
  </section>

  <div class="abs new-request">NEW REQUEST</div>

  <!-- Recent Completed Requests -->
  <section class="panel" style="left:522px;top:799px;width:380px;height:167px">
    <div class="panel-title">Recent Completed Requests</div>
    <table class="grid">
      <colgroup><col style="width:185px"><col></colgroup>
      <thead><tr style="height:26px"><th>Request No.</th><th>Completed Date</th></tr></thead>
      <tbody>
        <tr style="height:24px"><td><a href="#">56-0003</a></td><td>20/4/2013</td></tr>
        <tr style="height:21px"><td><a href="#">56-0004</a></td><td>21/4/2013</td></tr>
        <tr class="filler" style="height:27px;vertical-align:top"><td style="padding-top:1px"><a href="#">56-0004</a></td><td style="padding-top:1px">21/4/2013</td></tr>
      </tbody>
    </table>
    <div class="pager" style="height:31px">
      <svg width="8" height="12" viewBox="0 0 8 12"><path d="M6 1L1.5 6 6 11" fill="none" stroke="#3aa8df" stroke-width="2"/></svg><span>1</span><span>2</span><span>3</span><span>4</span><svg width="8" height="12" viewBox="0 0 8 12"><path d="M2 1l4.5 5L2 11" fill="none" stroke="#3aa8df" stroke-width="2"/></svg>
    </div>
  </section>

  <footer class="abs site-footer">
    <div class="footer-links"><span>Home</span><span>|</span><span>Permits</span><span>|</span><span>Search</span><span>|</span><span>Report</span><span>|</span><span>Admin</span><span>|</span><span>Help</span></div>
    <div class="copyright">©2013 Northgate Chemical| All Rights Reserved</div>
  </footer>

</div>
</body>
</html>
```